KAJU Freightways #ALLKAJU Business Cards & Letterhead

I am looking to business cards designed for our organization. We are currently undergoing a small re-branding that is taking place. Our organization is called KAJU Freightways and we are headquartered in Phoenix, AZ. We primarily provide transportation and logistics services to the Marlow Parcel Bureau who is our largest customer. I would like to see a design that incorporates name, title, contact info, website, and address (this will be different depending on the employee). I would also like to see some color on the business card using our logo colors or a variation. I would like our logo on the back of the business card with the website displayed. The final design should communicate that we are a next generation transportation operate that focuses on being driver-first, customer-centric, innovative, and sustainable.We would also like our #ALLKAJU catch phrase incorporated as well.

Target Market(s)

Transportation & Logistics

Industry/Entity Type

Trucking Company

Contact Information for Business Card

-First and Last Name
-Position Title
-Contact Phone
-Contact Email
-Physical Address

Font styles to use
Serif

Colors

Designer to choose colors to be used in the design.

Requirements
Must have
• -KAJU logo prominently displayed
• -#ALLKAJU catch phrase used
• -Some amount of color, design gradient, etc.
• -Logo on the back with website listed (https://www.kajufreightco.example)

```html
<!DOCTYPE html>
<html lang="en">
<head>
<meta charset="utf-8">
<title>KAJU Freightways Business Card</title>
<link href="https://fonts.googleapis.com/css2?family=Lora:wght@400;600;700&display=swap" rel="stylesheet">
<style>
  :root {
    --bg: #2a2c2e;
    --card-light: #fbfcfb;
    --card-dark: #063843;
    --brand-dark: #0b3a44;
    --brand-green: #6cbf3a;
    --text-soft: #9fb1b5;
    --text-light: #dbe3e4;
    --silver: #c7cbcd;
    --rule: #8ea2a6;
  }
  * { margin: 0; padding: 0; box-sizing: border-box; }
  html, body { width: 1200px; height: 960px; overflow: hidden; }
  body {
    background: var(--bg);
    font-family: "Lora", serif;
    position: relative;
  }
  .card {
    position: absolute;
    left: 250px;
    width: 700px;
    height: 400px;
    box-shadow: 0 10px 30px rgba(0,0,0,.45);
    overflow: hidden;
  }
  .card--front { top: 60px; background: var(--card-light); }
  .card--back { top: 500px; background: var(--card-dark); }

  .front-texture {
    position: absolute; inset: 0;
    background: radial-gradient(circle at 50% 50%, #ffffff 0%, #f1f4f1 70%, #e9eeea 100%);
  }
  .front-mark {
    position: absolute; left: 50%; top: 50%;
    transform: translate(-50%, -50%);
    display: flex; align-items: center; gap: 16px;
  }
  .front-mark .dot {
    width: 34px; height: 34px; border-radius: 50%;
    border: 5px solid var(--brand-green);
  }
  .front-mark .name {
    font-weight: 700; font-size: 78px; letter-spacing: 2px;
    color: var(--brand-dark); line-height: 1;
  }

  .contact { position: absolute; left: 44px; top: 116px; }
  .contact .person {
    font-weight: 700; font-size: 25px; letter-spacing: 1.5px;
    color: var(--brand-green); text-transform: uppercase;
  }
  .contact .role { font-size: 16px; font-style: italic; color: var(--text-soft); margin-top: 2px; }
  .contact ul { list-style: none; margin-top: 14px; }
  .contact li {
    display: flex; align-items: center; gap: 10px;
    font-size: 16px; color: var(--text-light); line-height: 24px;
  }
  .contact svg { width: 13px; height: 13px; fill: var(--brand-green); flex: none; }
  .rule {
    position: absolute; left: 44px; right: 44px; top: 304px;
    height: 1px; background: var(--rule);
  }
  .address {
    position: absolute; left: 44px; top: 318px;
    display: flex; align-items: center; gap: 10px;
    font-size: 17px; color: var(--text-light);
  }
  .address svg { width: 14px; height: 16px; fill: var(--brand-green); }

  .back-brand {
    position: absolute; right: 56px; top: 92px;
    display: flex; flex-direction: column; align-items: flex-end; gap: 10px;
  }
  .back-mark { display: flex; align-items: center; gap: 12px; }
  .back-mark .dot {
    width: 26px; height: 26px; border-radius: 50%;
    border: 4px solid var(--silver);
  }
  .back-mark .name {
    font-weight: 700; font-size: 58px; letter-spacing: 2px;
    color: var(--silver); line-height: 1;
  }
  .tagline {
    font-weight: 600; font-size: 16px; letter-spacing: 2px;
    color: var(--brand-green);
  }
</style>
</head>
<body>
  <section class="card card--front">
    <div class="front-texture" role="img" aria-label="Faint repeating brand pattern on textured white stock"></div>
    <div class="front-mark">
      <span class="dot"></span>
      <span class="name">KAJU</span>
    </div>
  </section>

  <section class="card card--back">
    <div class="contact">
      <p class="person">Dorian Pell</p>
      <p class="role">President</p>
      <ul>
        <li><svg viewBox="0 0 24 24"><path d="M6.6 10.8a15 15 0 0 0 6.6 6.6l2.2-2.2c.3-.3.7-.4 1-.2 1.1.4 2.3.6 3.6.6.6 0 1 .4 1 1V20c0 .6-.4 1-1 1A17 17 0 0 1 3 4c0-.6.4-1 1-1h3.5c.6 0 1 .4 1 1 0 1.3.2 2.5.6 3.6.1.3 0 .7-.2 1z"/></svg>480-555-0173</li>
        <li><svg viewBox="0 0 24 24"><path d="M2 5h20v14H2zM4 7v.5l8 5 8-5V7l-8 5z"/></svg>dpell@kajufreightco.example</li>
        <li><svg viewBox="0 0 24 24"><path d="M12 2a10 10 0 1 0 0 20 10 10 0 0 0 0-20zm-1 17.9A8 8 0 0 1 4 12l5 5v1a2 2 0 0 0 2 2zm6.9-2.5A2 2 0 0 0 16 16h-1v-3a1 1 0 0 0-1-1H8v-2h2a1 1 0 0 0 1-1V7h2a2 2 0 0 0 2-2v-.4a8 8 0 0 1 2.9 12.8z"/></svg>www.kajufreightco.example</li>
      </ul>
    </div>
    <div class="rule"></div>
    <p class="address"><svg viewBox="0 0 24 28"><path d="M12 0a10 10 0 0 0-10 10c0 7.5 10 18 10 18s10-10.5 10-18A10 10 0 0 0 12 0zm0 14a4 4 0 1 1 0-8 4 4 0 0 1 0 8z"/></svg>2140 Saguaro Way Phoenix, Arizona 85004</p>
    <div class="back-brand">
      <div class="back-mark">
        <span class="dot"></span>
        <span class="name">KAJU</span>
      </div>
      <p class="tagline">#ALLKAJU</p>
    </div>
  </section>
</body>
</html>
```